tinyTally Resource Book - 10 maths tasks to do outside

I need a 22 (11 pages back to back) page A6 sized book produced to standard for submission to professional printer. Needs to be as .pdf file showing guide lines and allowances for colour bleed. I have text already written and submitted as attachment in a Word file with margins set to A6 size. The theme of the materials is "Nature Play" so using lots of pictures from nature (Australia preferably) and showing lots of patterns in nature (rocks, leaves, flower petals etc). Some of the tasks refer to specific activities, such as "shadows" and "floating" so would be great to illustrate appropriately. The big emphasis is on learning outside the classroom, getting kids to engage actively with nature. I would like to see the pages as full colour - so not white background. The book itself will be spiral bound along the top edge so a margin of at least 1cm will be required at the top of each page (or the bottom of even numbered pages). Book will be printed on plastic laminated matte paper for outdoor use. Font size needs to be big enough to read. Fonts sizes, alignments and page numbers are all different at the moment and need to be standardised. One photo is included in a page as a sample if you can use it, otherwise disregard. Logo for Wattlebrook Numeracy Guild is also included to have as part of the acknowledgements at the back of the book.

Target Market(s)

Book is for early childhood and preschool teachers.

Industry/Entity Type

Education

Font styles to use
Sans Serif

Requirements
Must have
• Colour and appeal.
Nice to have
• Use of natural colours instead of bright catchy colours but that is your call.
Should not have
• American spelling

```html
<!DOCTYPE html>
<html lang="en-AU">
<head>
<meta charset="utf-8">
<title>tinyTally – 4. One More</title>
<link rel="stylesheet" href="https://fonts.googleapis.com/css2?family=Poppins:wght@700&family=Didact+Gothic&display=swap">
<style>
  :root {
    --paper: #ffffff;
    --crop: #555555;
    --wood-light: #eec08c;
    --wood-mid: #e2aa72;
    --wood-dark: #d89a60;
    --heading: #2e3a8f;
    --heading-edge: #ffffff;
    --body-text: #3d3a52;
    --bullet: #d9262c;
    --leaf-light: #d8ea6a;
    --leaf-dark: #8fc13e;
  }
  * { margin: 0; padding: 0; box-sizing: border-box; }
  html, body { width: 892px; height: 1200px; overflow: hidden; background: var(--paper); }
  .page { position: relative; width: 892px; height: 1200px; }
  .crop-marks { position: absolute; inset: 0; }
  .wood-panel {
    position: absolute; left: 54px; top: 54px; width: 784px; height: 1092px;
    background: linear-gradient(90deg, var(--wood-mid) 0%, var(--wood-light) 18%, var(--wood-mid) 34%, var(--wood-light) 52%, var(--wood-dark) 68%, var(--wood-light) 84%, var(--wood-mid) 100%);
  }
  .leaf-sprig {
    position: absolute; left: 540px; top: 836px; width: 250px; height: 230px;
    background: radial-gradient(ellipse at center, var(--leaf-light) 0%, var(--leaf-dark) 45%, rgba(143,193,62,0) 72%);
    opacity: .85;
  }
  .content { position: absolute; left: 124px; top: 138px; width: 660px; }
  h1, h2 {
    font-family: "Poppins", sans-serif; font-weight: 700; color: var(--heading);
    text-shadow: -2px -2px 0 var(--heading-edge), 2px -2px 0 var(--heading-edge), -2px 2px 0 var(--heading-edge), 2px 2px 0 var(--heading-edge), 4px 4px 4px rgba(0,0,0,.35);
    letter-spacing: .5px;
  }
  h1 { font-size: 49px; line-height: 60px; }
  h2 { font-size: 39px; line-height: 50px; margin-top: 20px; }
  .task-list { list-style: none; margin-left: 62px; margin-top: 2px; }
  .task-list li {
    position: relative; padding-left: 32px;
    font-family: "Didact Gothic", sans-serif; font-size: 27px; line-height: 36.5px; color: var(--body-text);
  }
  .task-list li::before {
    content: ""; position: absolute; left: 2px; top: 10px; width: 15px; height: 15px;
    background: var(--bullet); transform: rotate(45deg);
  }
</style>
</head>
<body>
<div class="page">
  <div class="wood-panel" role="img" aria-label="Light bamboo wood grain background"></div>
  <svg class="crop-marks" width="892" height="1200" aria-hidden="true">
    <g stroke="var(--crop)" stroke-width="1">
      <line x1="54" y1="0" x2="54" y2="40"/><line x1="74" y1="36" x2="74" y2="74"/>
      <line x1="0" y1="54" x2="40" y2="54"/><line x1="36" y1="74" x2="74" y2="74"/>
      <line x1="838" y1="0" x2="838" y2="40"/><line x1="818" y1="36" x2="818" y2="74"/>
      <line x1="852" y1="54" x2="892" y2="54"/><line x1="818" y1="74" x2="856" y2="74"/>
      <line x1="54" y1="1160" x2="54" y2="1200"/><line x1="74" y1="1126" x2="74" y2="1164"/>
      <line x1="0" y1="1146" x2="40" y2="1146"/><line x1="36" y1="1126" x2="74" y2="1126"/>
      <line x1="838" y1="1160" x2="838" y2="1200"/><line x1="818" y1="1126" x2="818" y2="1164"/>
      <line x1="852" y1="1146" x2="892" y2="1146"/><line x1="818" y1="1126" x2="856" y2="1126"/>
    </g>
  </svg>
  <div class="leaf-sprig" role="img" aria-label="Two sprigs of fresh green leaves"></div>
  <main class="content">
    <h1>4. One More</h1>
    <ul class="task-list">
      <li>Make a line of objects</li>
      <li>Ask partner to make a line of similar objects “and one more”</li>
    </ul>
    <h2>Prompting questions</h2>
    <ul class="task-list">
      <li>Can you make a line that uses the same number of objects as the first line but it is longer? shorter? (by changing the spacing between objects)</li>
    </ul>
    <h2>Variations</h2>
    <ul class="task-list">
      <li>Make a line that is “one less”, “two more”</li>
      <li>Make more lines of the same number of objects beneath the first line to make a rectangle</li>
      <li>Change orientation of line from hori-<br>zontal to vertical or diagonal</li>
    </ul>
    <h2>Big Ideas</h2>
    <ul class="task-list">
      <li>One-to-one correspondence</li>
      <li>Equivalence</li>
      <li>More than, less than</li>
    </ul>
  </main>
</div>
</body>
</html>
```